New professional Training Site

I need a basic 4-page Wordpress website using an existing logo that I will supply.  I would like appropriate images to complement the text which I have provided. I would like a link on the landing page to a brochure of 4 pages, which I shall also provide.

I have attached the various Logo files, the text for the pages, and the pages of the brochure.
Here is the brochure in question: https://www.plivomarket.com/design/28021656

The market is professional business training, and the target audience is buyers and sellers of businesses.

I would like an editable box on the landing page to list ‘Future Events’.

Updates
I still have no access to the site I want made over, so there is nothing we can do at present.

Target Market(s)
Buyers and sellers of businesses
Industry/Entity Type
Professional Training
Coding
Coded - Design and coding required
Number of Pages Required
4 page
Font styles to use
Other font styles liked:
- Helvetica Neue

Requirements
Must have
- The 4 pages structure as set out in the attached word doc. An editable box on the landing page for "Upcoming Events'

Nice to have
- I want the designs to feature the colours and log attached.

```html
<!DOCTYPE html>
<html lang="en">
<head>
<meta charset="utf-8">
<title>Deal Forge – Professional Business Training</title>
<link href="https://fonts.googleapis.com/css2?family=Montserrat:wght@600;700&family=Roboto:wght@400;500;700&display=swap" rel="stylesheet">
<style>
:root{
  --navy:#0c2554;
  --navy-deep:#09204a;
  --red:#7d0a12;
  --red-bright:#9c1018;
  --white:#ffffff;
  --ink:#1b1b1b;
  --grey:#5c5c5c;
  --mist:#eef1f6;
}
*{margin:0;padding:0;box-sizing:border-box}
html,body{width:1200px;height:3277px;overflow:hidden}
body{position:relative;background:var(--white);font-family:Roboto,"Helvetica Neue",Arial,sans-serif;color:var(--ink)}
.abs{position:absolute}
svg{display:block}

/* header */
.brand{position:absolute;display:flex;align-items:center;gap:10px}
.brand-dot{width:52px;height:52px;border-radius:50%;background:var(--navy)}
.brand-name{font-family:Montserrat,Arial,sans-serif;font-weight:700;font-size:26px;line-height:1;color:var(--red);letter-spacing:.5px}
.social{position:absolute;top:31px;left:668px;display:flex;gap:4px}
.social span{width:34px;height:34px;border-radius:50%;background:var(--red);display:block}
.hotline{position:absolute;left:868px;top:24px;display:flex;gap:14px;align-items:center}
.hotline-label{font-size:14px;font-weight:700;color:var(--ink)}
.hotline-number{font-size:21px;font-weight:700;color:var(--red);margin-top:2px;letter-spacing:.3px}

.main-nav{position:absolute;top:96px;left:0;width:1200px;height:42px;background:var(--navy);display:flex;justify-content:center;align-items:center;gap:40px;padding-left:40px}
.main-nav a{color:var(--white);text-decoration:none;font-size:14px;font-weight:700;letter-spacing:.2px}

/* hero */
.hero-photo{position:absolute;top:138px;left:0;width:1200px;height:650px;
  background:
    radial-gradient(ellipse 220px 420px at 230px 520px,#8e1a22 0%,rgba(142,26,34,0) 70%),
    radial-gradient(ellipse 260px 460px at 1000px 520px,#3a3b42 0%,rgba(58,59,66,0) 72%),
    radial-gradient(ellipse 300px 200px at 600px 320px,#e9eef2 0%,rgba(233,238,242,0) 75%),
    linear-gradient(90deg,#7a4a42 0%,#b7a296 22%,#dcdcd9 45%,#d2d7da 62%,#7a7676 82%,#3c3b40 100%)}
.hero-shade{position:absolute;inset:0;background:rgba(20,26,40,.22)}
.hero-title{position:absolute;top:268px;left:0;width:1200px;text-align:center;font-family:Montserrat,Arial,sans-serif;font-weight:700;font-size:31px;line-height:35px;color:var(--white)}
.hero-sub{position:absolute;top:394px;left:0;width:1200px;text-align:center;font-size:16px;line-height:24px;color:var(--white)}
.slide-arrow{position:absolute;top:374px;width:36px;height:36px;border-radius:50%;background:var(--white);display:flex;align-items:center;justify-content:center}

.btn{position:absolute;height:44px;border-radius:22px;display:flex;align-items:center;justify-content:center;gap:9px;color:var(--white);font-size:14px;font-weight:700;text-transform:uppercase;letter-spacing:.2px}
.btn-navy{background:var(--navy)}
.btn-red{background:var(--red)}

/* sections */
.city-fade{position:absolute;left:0;width:1200px;background:linear-gradient(180deg,#f4f6fa 0%,#e6ebf2 45%,#f7f8fb 100%)}
.section-heading{font-family:Montserrat,Arial,sans-serif;font-weight:700;color:var(--ink)}
.about-heading{position:absolute;left:111px;top:892px;font-size:30px;line-height:35px}
.about-text{position:absolute;left:111px;top:987px;width:447px;font-size:14.5px;line-height:25.8px;color:var(--grey);text-align:justify}

.navy-band{position:absolute;left:0;width:1200px;background:var(--navy)}
.package-heading{position:absolute;top:1512px;left:0;width:1200px;text-align:center;font-family:Montserrat,Arial,sans-serif;font-weight:700;font-size:31px;color:var(--white)}
.package{position:absolute;top:1572px;width:310px;text-align:center;color:var(--white)}
.package svg{margin:0 auto}
.package-title{font-size:20px;font-weight:700;margin-top:20px}
.package-text{font-size:14px;line-height:22px;margin-top:22px}
.package-link{display:inline-flex;align-items:center;gap:6px;margin-top:10px;font-size:12px;font-weight:700;color:var(--white);text-decoration:underline}

/* brochure */
.brochure{position:absolute;left:127px;top:2227px;width:392px;height:507px;background:#f5f5f5;box-shadow:0 4px 14px rgba(0,0,0,.35);display:flex;flex-direction:column;font-size:7px;line-height:9px}
.brochure-top{background:var(--navy);color:var(--white);height:93px;padding:20px 22px 0;position:relative}
.brochure-price{font-size:15px;font-weight:700;line-height:18px}
.brochure-includes{margin-top:6px;font-size:6.5px;line-height:8px;width:200px}
.brochure-brand{position:absolute;right:20px;top:22px;display:flex;align-items:center;gap:6px}
.brochure-brand .brand-dot{width:40px;height:40px;background:var(--white)}
.brochure-brand .brand-name{font-size:17px;color:var(--white)}
.brochure-bar{display:flex;background:var(--red);color:var(--white);font-size:11px;font-weight:500;height:24px;align-items:center}
.brochure-bar span{flex:1;padding-left:28px}
.brochure-body{flex:1;display:flex;padding:12px 0 0}
.brochure-col{flex:1;padding-left:28px;list-style:none}
.brochure-col li{color:var(--red-bright);font-weight:700;margin-bottom:14px;width:150px}
.brochure-col li.break{color:var(--red)}
.brochure-foot{background:var(--navy);color:var(--white);height:108px;padding:12px 24px}
.brochure-foot b{font-size:9.5px;display:block;margin-bottom:2px}
.brochure-foot p{font-size:6.5px;line-height:8px;margin-bottom:10px}

.member-heading{position:absolute;left:620px;top:2292px;font-size:30px;line-height:35px}
.member-list{position:absolute;left:620px;top:2360px;width:470px;list-style:none}
.member-list li{position:relative;padding-left:31px;font-size:14.5px;line-height:38.6px;color:var(--grey)}
.member-list li svg{position:absolute;left:0;top:13px}

.events-box{position:absolute;left:878px;top:2588px;width:250px;background:var(--white);border-top:4px solid var(--red);box-shadow:0 3px 12px rgba(12,37,84,.18);padding:10px 14px 12px}
.events-title{font-family:Montserrat,Arial,sans-serif;font-weight:700;font-size:14px;color:var(--navy);margin-bottom:6px}
.events-list{list-style:none}
.events-list li{display:flex;gap:10px;font-size:12.5px;line-height:19px;color:var(--grey)}
.events-list time{font-weight:700;color:var(--red);width:44px;flex:none}

/* footer */
.footer-col{position:absolute;top:2946px;color:var(--white)}
.footer-col h4{font-size:14px;font-weight:700;text-transform:uppercase;text-decoration:underline;text-underline-offset:4px;margin-bottom:24px}
.footer-col li{list-style:none;font-size:15px;line-height:33px}
.footer-col li::before{content:"»";margin-right:12px}
.footer-brand{position:absolute;left:874px;top:2958px;display:flex;align-items:center;gap:10px}
.footer-brand .brand-dot{background:var(--white)}
.footer-brand .brand-name{color:var(--white)}
.footer-address{position:absolute;left:874px;top:3040px;display:flex;gap:12px;font-size:15px;line-height:23px;color:var(--white)}
.contact-bar{position:absolute;left:163px;top:3122px;width:874px;height:57px;background:var(--red);display:flex;align-items:center}
.contact-item{display:flex;align-items:center;gap:18px;color:var(--white);font-size:16px;padding-left:22px;white-space:nowrap}
.contact-item:nth-child(1){width:260px}
.contact-item:nth-child(2){width:284px}
.contact-item:nth-child(3){flex:1}
.contact-item+.contact-item{border-left:1px solid rgba(255,255,255,.55)}
.contact-icon{width:40px;height:40px;border-radius:50%;border:1px solid rgba(255,255,255,.75);display:flex;align-items:center;justify-content:center;flex:none}
.copyright{position:absolute;top:3224px;left:0;width:1200px;text-align:center;color:var(--white);font-size:15px}
</style>
</head>
<body>

<!-- Header -->
<header>
  <div class="brand" style="left:112px;top:22px">
    <span class="brand-dot"></span>
    <span class="brand-name">DEAL FORGE</span>
  </div>
  <div class="social" aria-label="Social links"><span></span><span></span><span></span><span></span></div>
  <div class="hotline">
    <svg width="44" height="44" viewBox="0 0 24 24" fill="none" stroke="var(--red)" stroke-width="2" stroke-linecap="round"><path d="M4 14v-2a8 8 0 0 1 16 0v2"/><rect x="2.5" y="13" width="4" height="6" rx="1" fill="var(--red)"/><rect x="17.5" y="13" width="4" height="6" rx="1" fill="var(--red)"/><path d="M19.5 19c0 2-2 3-5 3"/></svg>
    <div>
      <div class="hotline-label">24 HOURS SERVICE</div>
      <div class="hotline-number">+ 1 555 204 7781</div>
    </div>
  </div>
  <nav class="main-nav">
    <a href="#">HOME</a><a href="#">ABOUT</a><a href="#">OUR SERVICES</a><a href="#">BLOG</a><a href="#">REVIEWS</a><a href="#">WHY US</a><a href="#">CONTACT</a>
  </nav>
</header>

<!-- Hero -->
<section class="hero">
  <div class="hero-photo" role="img" aria-label="Two businesswomen shaking hands in a bright office"><div class="hero-shade"></div></div>
  <h1 class="hero-title">We are a small group of<br>experienced entrepreneurs , bankers<br>accountants</h1>
  <p class="hero-sub">Lorem ipsum dolor sit amet, consectetur adipiscing elit, sed do eiusmod<br>tempor incididunt ut labore et dolore</p>
  <div class="btn btn-navy" style="left:420px;top:473px;width:197px">Let’s get started
    <svg width="13" height="13" viewBox="0 0 16 16"><circle cx="8" cy="8" r="7.5" fill="#fff"/><path d="M7 5l3 3-3 3" stroke="var(--navy)" stroke-width="2" fill="none"/></svg></div>
  <div class="btn btn-red" style="left:634px;top:473px;width:146px">Book now
    <svg width="13" height="13" viewBox="0 0 16 16"><circle cx="8" cy="8" r="7.5" fill="#fff"/><path d="M7 5l3 3-3 3" stroke="var(--red)" stroke-width="2" fill="none"/></svg></div>
  <div class="slide-arrow" style="left:31px"><svg width="12" height="12" viewBox="0 0 12 12"><path d="M8 1L3 6l5 5" stroke="#222" stroke-width="2" fill="none"/></svg></div>
  <div class="slide-arrow" style="left:1126px"><svg width="12" height="12" viewBox="0 0 12 12"><path d="M4 1l5 5-5 5" stroke="#222" stroke-width="2" fill="none"/></svg></div>
</section>

<!-- About -->
<div class="city-fade" style="top:760px;height:640px" role="img" aria-label="Faint city skyline backdrop"></div>
<svg class="abs" style="left:0;top:690px" width="1200" height="180" viewBox="0 0 1200 180">
  <path d="M0 95 C250 10 650 0 1200 30 L1200 70 C700 40 300 50 0 125 Z" fill="var(--navy)"/>
  <path d="M0 125 C300 50 700 40 1200 70 L1200 78 C700 52 300 62 0 132 Z" fill="#fff"/>
  <path d="M0 132 C300 62 700 52 1200 78 L1200 160 C950 110 600 90 300 115 C180 125 80 135 0 150 Z" fill="var(--red)"/>
  <path d="M0 150 C80 135 180 125 300 115 C600 90 950 110 1200 160 L1200 180 L0 180 Z" fill="#f4f6fa"/>
</svg>

<section class="about">
  <h2 class="section-heading about-heading">A new approach to buying<br>or selling a business</h2>
  <p class="about-text">We are a small group of experienced entrepreneurs, bankers, accountants, and others who have between us many decades of buying, selling, and founding businesses of all types and sizes, few if any of which had a turnover of less than several £ millions. We provide both first-time entrepreneurs and more experienced deal-doers with an unrivalled package of help, services, and support to enable them to successfully acquire SME businesses. We believe that the skills we provide at our workshops although vital are not enough on their own.</p>
  <div class="btn btn-navy" style="left:111px;top:1237px;width:164px">Learn more
    <svg width="13" height="13" viewBox="0 0 16 16"><circle cx="8" cy="8" r="7.5" fill="#fff"/><path d="M7 5l3 3-3 3" stroke="var(--navy)" stroke-width="2" fill="none"/></svg></div>
  <svg class="abs" style="left:636px;top:876px" width="446" height="446" viewBox="0 0 446 446" role="img" aria-label="Speaker presenting to a seated audience at a workshop">
    <defs>
      <linearGradient id="aboutPhoto" x1="0" y1="0" x2="0" y2="1"><stop offset="0" stop-color="#eef0f2"/><stop offset=".5" stop-color="#d3d6da"/><stop offset=".72" stop-color="#6d7382"/><stop offset="1" stop-color="#2d3446"/></linearGradient>
      <radialGradient id="aboutFocus" cx=".35" cy=".42" r=".25"><stop offset="0" stop-color="#1e2433" stop-opacity=".55"/><stop offset="1" stop-color="#1e2433" stop-opacity="0"/></radialGradient>
    </defs>
    <circle cx="223" cy="223" r="222" fill="var(--navy)"/>
    <circle cx="223" cy="223" r="222" fill="none" stroke="#fff" stroke-width="3" stroke-dasharray="2 60"/>
    <circle cx="223" cy="223" r="203" fill="var(--red)"/>
    <circle cx="223" cy="223" r="195" fill="#fff"/>
    <circle cx="223" cy="223" r="190" fill="url(#aboutPhoto)"/>
    <circle cx="223" cy="223" r="190" fill="url(#aboutFocus)"/>
  </svg>
</section>

<!-- Packages -->
<svg class="abs" style="left:0;top:1340px" width="1200" height="170" viewBox="0 0 1200 170">
  <path d="M0 60 C200 140 450 150 700 95 C900 50 1080 25 1200 20 L1200 170 L0 170 Z" fill="var(--navy)"/>
  <path d="M0 55 C200 130 420 145 640 105 C430 165 200 160 0 85 Z" fill="var(--red)"/>
</svg>
<div class="navy-band" style="top:1500px;height:560px"></div>

<section class="packages">
  <h2 class="package-heading">Our package</h2>

  <div class="package" style="left:120px">
    <svg width="276" height="276" viewBox="0 0 276 276" role="img" aria-label="Group workshop session in a bright classroom">
      <defs><radialGradient id="pkgWorkshop" cx=".5" cy=".35" r=".7"><stop offset="0" stop-color="#efe9df"/><stop offset=".55" stop-color="#b9ad9c"/><stop offset="1" stop-color="#4e4a48"/></radialGradient></defs>
      <circle cx="138" cy="140" r="131" fill="url(#pkgWorkshop)"/>
      <path d="M18 100 A125 125 0 0 1 258 100" stroke="var(--red)" stroke-width="7" fill="none"/>
    </svg>
    <div class="package-title">Deal Forge Workshop</div>
    <p class="package-text">Deal Forge Workshop will help you to identify some of the types of businesses and traps to be avoided, give you a sound</p>
    <a class="package-link">LEARN MORE <svg width="11" height="11" viewBox="0 0 16 16"><circle cx="8" cy="8" r="7.5" fill="#fff"/><path d="M7 5l3 3-3 3" stroke="var(--navy)" stroke-width="2" fill="none"/></svg></a>
  </div>

  <div class="package" style="left:452px">
    <svg width="276" height="276" viewBox="0 0 276 276" role="img" aria-label="Two advisers in conversation at a meeting table">
      <defs><radialGradient id="pkgAdvice" cx=".5" cy=".3" r=".75"><stop offset="0" stop-color="#c9ccd2"/><stop offset=".5" stop-color="#5b6170"/><stop offset="1" stop-color="#1f2431"/></radialGradient></defs>
      <circle cx="138" cy="138" r="131" fill="url(#pkgAdvice)"/>
      <path d="M18 100 A125 125 0 0 1 258 100" stroke="var(--navy-deep)" stroke-width="7" fill="none"/>
      <path d="M30 200 A125 125 0 0 0 246 200" stroke="var(--red)" stroke-width="7" fill="none"/>
    </svg>
    <div class="package-title">Deals Advice Line</div>
    <p class="package-text">Deals Advice Line is available to all members of The Founders' Circle . It is a use-as-needed quick answers service</p>
    <a class="package-link">LEARN MORE <svg width="11" height="11" viewBox="0 0 16 16"><circle cx="8" cy="8" r="7.5" fill="#fff"/><path d="M7 5l3 3-3 3" stroke="var(--navy)" stroke-width="2" fill="none"/></svg></a>
  </div>

  <div class="package" style="left:784px">
    <svg width="276" height="276" viewBox="0 0 276 276" role="img" aria-label="Business partners shaking hands in a modern office">
      <defs><radialGradient id="pkgCircle" cx=".5" cy=".3" r=".75"><stop offset="0" stop-color="#e7ebee"/><stop offset=".55" stop-color="#a5aeb6"/><stop offset="1" stop-color="#2e3440"/></radialGradient></defs>
      <circle cx="138" cy="140" r="131" fill="url(#pkgCircle)"/>
      <path d="M18 100 A125 125 0 0 1 258 100" stroke="var(--red)" stroke-width="7" fill="none"/>
    </svg>
    <div class="package-title">The Founders' Circle</div>
    <p class="package-text">The Founders' Circle is a proper club. It will provide you with a reliable source of help, encouragement, and support.</p>
    <a class="package-link">LEARN MORE <svg width="11" height="11" viewBox="0 0 16 16"><circle cx="8" cy="8" r="7.5" fill="#fff"/><path d="M7 5l3 3-3 3" stroke="var(--navy)" stroke-width="2" fill="none"/></svg></a>
  </div>
</section>

<!-- Membership -->
<div class="city-fade" style="top:2150px;height:640px" role="img" aria-label="Faint city skyline backdrop"></div>
<svg class="abs" style="left:0;top:2030px" width="1200" height="180" viewBox="0 0 1200 180">
  <path d="M0 0 L1200 0 L1200 30 C900 30 620 60 420 110 C260 150 110 130 0 70 Z" fill="var(--navy)"/>
  <path d="M0 70 C110 130 260 150 420 110 C620 60 900 30 1200 30 L1200 44 C900 46 650 90 460 140 C270 188 110 160 0 100 Z" fill="var(--red)"/>
</svg>

<section class="membership">
  <article class="brochure" aria-label="Workshop brochure">
    <div class="brochure-top">
      <div class="brochure-price">Cost £1,999 plus VAT</div>
      <div class="brochure-includes">This includes: meals and refreshments; post-event networking reception; two months Founders' Circle membership.</div>
      <div class="brochure-brand"><span class="brand-dot"></span><span class="brand-name">DEAL FORGE</span></div>
    </div>
    <div class="brochure-bar"><span>Content - Morning</span><span>Content – Afternoon</span></div>
    <div class="brochure-body">
      <ul class="brochure-col">
        <li>8.45AM - Opening Remarks</li>
        <li>9.00AM - What am I looking for</li>
        <li>10.00AM - Valuing the business &amp; Negotiating the Deal</li>
        <li class="break">11.00AM Coffee Break</li>
        <li>11.15AM - Debt Finance</li>
        <li class="break">12.15PM - Lunch Break</li>
      </ul>
      <ul class="brochure-col">
        <li>1.00PM - Financing the deal</li>
        <li>2.00PM - The Role and Importance of Due Diligence</li>
        <li class="break">3.00PM Coffee Break</li>
        <li>3.15PM - Legal Completion</li>
        <li>4.15PM - Negotiating Skills</li>
        <li>5.00PM Refreshments &amp; Networking</li>
      </ul>
    </div>
    <div class="brochure-foot">
      <b>What is Deal Forge?</b>
      <p>Practical workshops for buyers and sellers of growing businesses.</p>
      <b>The Founders' Circle*</b>
      <p>A members club offering help, support and shared deal experience.</p>
    </div>
  </article>

  <h2 class="section-heading member-heading">Membership includes</h2>
  <ul class="member-list">
    <li><svg width="14" height="14" viewBox="0 0 16 16"><circle cx="8" cy="8" r="7.5" fill="var(--red)"/><path d="M7 5l3 3-3 3" stroke="#fff" stroke-width="2" fill="none"/></svg>Access to the Deals Advice Line for practical and technical support</li>
    <li><svg width="14" height="14" viewBox="0 0 16 16"><circle cx="8" cy="8" r="7.5" fill="var(--red)"/><path d="M7 5l3 3-3 3" stroke="#fff" stroke-width="2" fill="none"/></svg>The Deal Forge Model, which can be used either as a quick business valuation and funding tool, or in expanded form as a complete business plan and forecast.</li>
    <li><svg width="14" height="14" viewBox="0 0 16 16"><circle cx="8" cy="8" r="7.5" fill="var(--red)"/><path d="M7 5l3 3-3 3" stroke="#fff" stroke-width="2" fill="none"/></svg>The members Club website</li>
    <li><svg width="14" height="14" viewBox="0 0 16 16"><circle cx="8" cy="8" r="7.5" fill="var(--red)"/><path d="M7 5l3 3-3 3" stroke="#fff" stroke-width="2" fill="none"/></svg>The deal structuring and funding services of Bridgeway Finance.</li>
  </ul>
  <div class="btn btn-navy" style="left:621px;top:2618px;width:164px">Learn more
    <svg width="13" height="13" viewBox="0 0 16 16"><circle cx="8" cy="8" r="7.5" fill="#fff"/><path d="M7 5l3 3-3 3" stroke="var(--navy)" stroke-width="2" fill="none"/></svg></div>

  <aside class="events-box" contenteditable="true" aria-label="Upcoming events, editable">
    <h3 class="events-title">Upcoming Events</h3>
    <ul class="events-list">
      <li><time>12 Mar</time>Deal Forge Workshop</li>
      <li><time>24 Apr</time>Founders' Circle Evening</li>
    </ul>
  </aside>
</section>

<!-- Footer -->
<svg class="abs" style="left:0;top:2750px" width="1200" height="180" viewBox="0 0 1200 180">
  <path d="M0 20 C220 95 420 125 700 60 C900 18 1080 8 1200 20 L1200 180 L0 180 Z" fill="var(--red)"/>
  <path d="M0 62 C250 135 500 148 760 104 C950 72 1100 64 1200 82 L1200 180 L0 180 Z" fill="#fff"/>
  <path d="M0 72 C250 145 500 158 760 114 C950 82 1100 74 1200 92 L1200 180 L0 180 Z" fill="var(--navy)"/>
</svg>
<footer>
  <div class="navy-band" style="top:2925px;height:352px"></div>
  <div class="footer-col" style="left:115px"><h4>Quick links</h4><ul><li>Home</li><li>About Us</li><li>Services</li></ul></div>
  <div class="footer-col" style="left:383px"><h4>Other links</h4><ul><li>Terms Of Use</li><li>Privacy Policy</li><li>Contact Us</li></ul></div>
  <div class="footer-col" style="left:653px"><h4>Useful links</h4><ul><li>Sitemap</li><li>Latest Blog</li><li>Help Service</li></ul></div>
  <div class="footer-brand"><span class="brand-dot"></span><span class="brand-name">DEAL FORGE</span></div>
  <div class="footer-address">
    <svg width="12" height="16" viewBox="0 0 12 16" style="margin-top:3px"><path d="M6 0a6 6 0 0 0-6 6c0 4.5 6 10 6 10s6-5.5 6-10a6 6 0 0 0-6-6z" fill="#fff"/><circle cx="6" cy="6" r="2.2" fill="var(--navy)"/></svg>
    <span>4120 Harbor Road Suite 210<br>United States</span>
  </div>
  <div class="contact-bar">
    <div class="contact-item"><span class="contact-icon"><svg width="16" height="16" viewBox="0 0 24 24"><path d="M6.6 10.8a15 15 0 0 0 6.6 6.6l2.2-2.2a1 1 0 0 1 1-.25 11.4 11.4 0 0 0 3.6.57 1 1 0 0 1 1 1V20a1 1 0 0 1-1 1A17 17 0 0 1 3 4a1 1 0 0 1 1-1h3.5a1 1 0 0 1 1 1c0 1.25.2 2.45.57 3.57a1 1 0 0 1-.25 1z" fill="#fff"/></svg></span>+1 555 2047 781</div>
    <div class="contact-item"><span class="contact-icon"><svg width="16" height="16" viewBox="0 0 24 24" fill="none" stroke="#fff" stroke-width="2"><rect x="5" y="2" width="14" height="20" rx="2"/><path d="M9 7h6M9 11h2M13 11h2M9 15h2M13 15h2"/></svg></span>+1 555 3190 642</div>
    <div class="contact-item"><span class="contact-icon"><svg width="16" height="16" viewBox="0 0 24 24" fill="none" stroke="#fff" stroke-width="2"><rect x="2" y="5" width="20" height="14" rx="2"/><path d="M2 7l10 7 10-7"/></svg></span>info@dealforge-academy.com</div>
  </div>
  <p class="copyright">© 2022 Deal Forge. All Rights Reserved</p>
</footer>

</body>
</html>
```